Moravel Aesthetic Doctor

I require an elegant, luxurious looking business card for my aesthetic business. I am a doctor and that will set me aside from competitors. I am planning to provide home and spa based treatments to clients with high expectations. I have attached my logo.

```html
<!DOCTYPE html>
<html lang="en">
<head>
<meta charset="utf-8">
<title>Moravel Aesthetic Doctor – Business Card</title>
<link href="https://fonts.googleapis.com/css2?family=Arimo:wght@400;700&display=swap" rel="stylesheet">
<style>
  :root {
    --backdrop: #6f6f6f;
    --card-blue: #7ecbec;
    --card-white: #ffffff;
    --ink-grey: #6d6e70;
    --accent-blue: #4fb8e8;
    --on-blue: #ffffff;
  }
  * { margin: 0; padding: 0; box-sizing: border-box; }
  html, body { width: 1200px; height: 900px; overflow: hidden; }
  body {
    background: var(--backdrop);
    font-family: "Arimo", Arial, sans-serif;
    position: relative;
  }
  .card {
    position: absolute;
    top: 217px;
    width: 308px;
    height: 499px;
    box-shadow: 2px 3px 3px rgba(0,0,0,0.35);
  }
  .card--front {
    left: 279px;
    background: var(--card-blue);
    border-radius: 0 62px 0 62px;
    color: var(--on-blue);
    text-align: center;
  }
  .card--back {
    left: 617px;
    background: var(--card-white);
    border-radius: 62px 0 62px 0;
    color: var(--ink-grey);
  }

  /* front */
  .front-brand {
    position: absolute; left: 0; right: 0; top: 112px;
    font-weight: 400; color: var(--on-blue);
  }
  .front-brand__name { font-size: 46px; letter-spacing: 3px; line-height: 1; text-transform: uppercase; }
  .front-brand__tagline { font-size: 18px; letter-spacing: 2px; margin-top: 8px; text-transform: uppercase; }
  .front-headline {
    position: absolute; left: 0; right: 0; top: 230px;
    font-size: 21px; line-height: 24px; text-transform: uppercase;
  }
  .service-list {
    position: absolute; left: 0; right: 0; top: 333px;
    list-style: none; font-size: 15px; line-height: 24.5px; text-transform: uppercase;
  }

  /* back */
  .back-brand {
    position: absolute; left: 34px; top: 126px;
    display: flex; align-items: center; gap: 14px;
    color: var(--ink-grey); font-weight: 400;
  }
  .back-brand__mark {
    width: 62px; height: 62px; border-radius: 50%;
    border: 2px solid var(--accent-blue); flex: none;
  }
  .back-brand__name { font-size: 32px; letter-spacing: 2px; line-height: 1; text-transform: uppercase; }
  .back-brand__tagline { font-size: 14px; letter-spacing: 1.6px; margin-top: 6px; text-transform: uppercase; }

  .practitioner { position: absolute; left: 34px; top: 294px; }
  .practitioner__name { font-size: 20px; font-weight: 700; color: var(--ink-grey); }
  .practitioner__letters { font-size: 13px; font-weight: 400; margin-left: 3px; }
  .practitioner__diploma { font-size: 15px; line-height: 18px; color: var(--accent-blue); margin-top: 2px; }

  .contact-list { position: absolute; left: 34px; top: 367px; list-style: none; font-size: 14.5px; }
  .contact-list li { display: flex; align-items: center; gap: 6px; height: 19.5px; }
  .contact-list li + li { margin-top: 0; }
  .contact-list svg { width: 13px; height: 13px; flex: none; }
  .contact-list .accent { color: var(--accent-blue); }

  .social { position: absolute; left: 35px; top: 442px; display: flex; gap: 4px; }
  .social__dot { width: 18px; height: 18px; border-radius: 50%; background: var(--accent-blue); }
  .social__dot--alt { background: #c24d8f; }
</style>
</head>
<body>

<section class="card card--front" aria-label="Card front">
  <div class="front-brand">
    <div class="front-brand__name">Moravel</div>
    <div class="front-brand__tagline">Aesthetic Doctor</div>
  </div>
  <p class="front-headline">Home and spa based<br>treatments</p>
  <ul class="service-list">
    <li>Dermal injectables</li>
    <li>Plasma facials</li>
    <li>Microneedling</li>
    <li>Skin boosters</li>
    <li>Excessive sweating</li>
  </ul>
</section>

<section class="card card--back" aria-label="Card back">
  <div class="back-brand">
    <span class="back-brand__mark"></span>
    <div>
      <div class="back-brand__name">Moravel</div>
      <div class="back-brand__tagline">Aesthetic Doctor</div>
    </div>
  </div>

  <div class="practitioner">
    <p class="practitioner__name">Dr Elise Varga<span class="practitioner__letters">MRCPCH MD</span></p>
    <p class="practitioner__diploma">Australasian Diploma of<br>Aesthetic Medicine</p>
  </div>

  <ul class="contact-list">
    <li>
      <svg viewBox="0 0 16 16" aria-hidden="true"><path d="M3.5 1.5l2.5 3-1.5 1.6c.8 2 2.4 3.6 4.4 4.4L10.5 9l3 2.5-1.3 2.3c-5.4-.3-9.7-4.6-10-10z" fill="none" stroke="#4fb8e8" stroke-width="1.4" stroke-linejoin="round"/></svg>
      <span>0800 555 014</span>
    </li>
    <li>
      <svg viewBox="0 0 16 16" aria-hidden="true"><rect x="1" y="3" width="14" height="10" fill="#4fb8e8"/><path d="M1 3l7 6 7-6" fill="none" stroke="#fff" stroke-width="1.2"/></svg>
      <span>elise@moravel.co.nz</span>
    </li>
    <li>
      <svg viewBox="0 0 16 16" aria-hidden="true"><g fill="none" stroke="#4fb8e8" stroke-width="1.2"><circle cx="8" cy="8" r="6.5"/><ellipse cx="8" cy="8" rx="3" ry="6.5"/><path d="M1.5 8h13M2.6 4.5h10.8M2.6 11.5h10.8"/></g></svg>
      <span>www.<span class="accent">moravel</span>.co.nz</span>
    </li>
  </ul>

  <div class="social" aria-label="Social profiles">
    <span class="social__dot"></span>
    <span class="social__dot social__dot--alt"></span>
  </div>
</section>

</body>
</html>
```